QuillVane needs a dashboard page designed

Redesign the dashboard shown in the provided images.

There are two images:
- dashboard.png
- dashboard-expanded.png

NOTE: The vocabulary navigation on the left will be a very long list of words 100s, so keep that in mind when you're designing both the vocab navigation and the expanded vocab popup.

In the dashboard.png picture, there needs to be a progress chart showing the word progress like the following: review 1(show it as completed) -> review 2(show the user they are here) -> review 3(unvisited) -> review 4(unvisited)

The do-not-design-this-page.png image is for your reference only. It is not to be designed. Use it to understand the overall look and feel of the website to help you create the best dashboard page possible.
Updates

Need extra days to review

Industry/Entity Type

Education English learning

Number of Pages Required

1 page

Requirements
Must have
• The main navigation and main header cannot change between pages. See the do-not-design page for the main navigateion and header.
Should not have
• Do not add a person profile. We will not have images of our users. Keep the icons in the main navigation as they are.

```html
<!DOCTYPE html>
<html lang="en">
<head>
<meta charset="utf-8">
<title>QuillVane Dashboard</title>
<link href="https://fonts.googleapis.com/css2?family=Poppins:wght@400;500;600&display=swap" rel="stylesheet">
<style>
:root{
  --page:#ffffff;
  --header:#1d1d1d;
  --rail:#0a6ab5;
  --nav:#1f242a;
  --nav-line:#2e353d;
  --nav-text:#d3d7dc;
  --content:#f4f4f4;
  --card:#efefef;
  --ink:#1e1e1e;
  --muted:#8a8a8a;
  --rule:#dcdcdc;
  --accent:#1a8fe0;
  --accent-dark:#0a6ab5;
  --link:#0a5fb0;
  --done:#3cb043;
  --star:#f5a623;
}
*{box-sizing:border-box;margin:0;padding:0}
html,body{width:1200px;height:611px;overflow:hidden;background:var(--page);font-family:'Poppins',sans-serif}
.screen{position:absolute;top:19px;width:1230px;height:1229px;transform:scale(.4659);transform-origin:0 0;overflow:hidden;background:var(--content)}
.screen.one{left:20px}
.screen.two{left:609px}
.abs{position:absolute}
.app-header{left:0;top:0;width:1230px;height:64px;background:var(--header)}
.brand{left:20px;top:16px;color:#fff;font-size:20px;font-weight:600;letter-spacing:.3px}
.header-icons{right:60px;top:24px;display:flex;gap:22px;align-items:center}
.rail{left:0;top:64px;width:101px;height:1165px;background:var(--rail)}
.rail-item{position:absolute;left:0;width:101px;text-align:center;color:#fff;font-size:10px;font-weight:600}
.rail-item svg{display:block;margin:0 auto 4px}
.vocab-nav{left:101px;top:64px;width:250px;height:1165px;background:var(--nav)}
.filter{position:absolute;width:91px;height:32px;border:1px solid #9aa2ab;border-radius:3px;color:#fff;font-size:11px;padding:7px 10px;display:flex;justify-content:space-between;align-items:center}
.filter.light{border-color:#b8b8b8;color:var(--ink);background:#fff}
.expand{position:absolute;left:148px;top:30px;color:#fff;font-size:11px;display:flex;gap:8px;align-items:center}
.nav-rule{position:absolute;left:0;width:250px;height:1px;background:var(--nav-line)}
.group-title{position:absolute;left:18px;color:#fff;font-size:13px;font-weight:600;display:flex;align-items:center;gap:13px}
.word{position:absolute;left:45px;color:var(--nav-text);font-size:13px;display:flex;gap:10px;align-items:center}
.word::before{content:"›";font-size:14px;color:#fff}
.word.active{left:28px;width:222px;height:34px;background:var(--rail);border-radius:17px 0 0 17px;color:#fff;font-weight:600;padding-left:13px}
.card{left:368px;top:84px;width:880px;height:1160px;background:var(--card);border-radius:8px}
.h2{position:absolute;left:384px;color:var(--ink);font-size:20px;font-weight:500}
.rule{position:absolute;left:384px;width:783px;height:1px;background:var(--rule)}
.step-line{position:absolute;left:456px;top:193px;width:636px;height:3px;background:#e2e2e2}
.step{position:absolute;top:167px;width:160px;margin-left:-80px;text-align:center}
.dot{width:54px;height:54px;border-radius:50%;margin:0 auto;display:flex;align-items:center;justify-content:center;border:3px solid #fff;box-shadow:0 0 0 2px var(--accent)}
.dot.todo{background:#8d8d8d;box-shadow:0 0 0 2px #8d8d8d;color:#fff;font-weight:600;font-size:20px}
.dot.done{background:var(--accent)}
.step-name{margin-top:8px;font-size:15px;font-weight:500;color:var(--ink)}
.step-state{font-size:17px;font-weight:500;color:#8d8d8d}
.step-state.ok{color:var(--done)}
.start-btn{left:384px;top:380px;width:308px;height:44px;background:#fff;border:1px solid #cfcfcf;display:flex;align-items:center;gap:16px;padding-left:20px;font-size:14px;color:var(--ink)}
.body-text{position:absolute;left:384px;width:790px;font-size:12.6px;line-height:23px;color:#2a2a2a}
.body-text b{color:var(--link);font-weight:600}
.chart{left:384px;top:640px}
.x10{left:1195px;top:1192px;font-size:13px;color:var(--muted)}
.overlay{left:0;top:0;width:1230px;height:1229px;background:rgba(0,0,0,.36)}
.modal{left:140px;top:154px;width:1014px;height:320px;background:#fff;border-radius:6px;box-shadow:0 6px 24px rgba(0,0,0,.25)}
.m-title{position:absolute;left:24px;color:var(--ink);font-size:13px;font-weight:600;display:flex;gap:14px;align-items:center}
.m-row{position:absolute;left:54px;display:flex;gap:22px;font-size:13px;color:var(--ink)}
.m-row span::before{content:"› ";font-weight:600;margin-right:6px}
.m-row .sel{color:var(--link);font-weight:600}
.m-rule{position:absolute;left:0;width:1014px;height:1px;background:#e4e4e4}
</style>
</head>
<body>

<!-- Dashboard -->
<div class="screen one">
  <div class="abs app-header">
    <div class="abs brand">QuillVane</div>
    <div class="abs header-icons">
      <svg width="14" height="14" viewBox="0 0 14 14"><circle cx="7" cy="7" r="5" fill="none" stroke="#fff" stroke-width="3" stroke-dasharray="2.4 1.5"/><circle cx="7" cy="7" r="2" fill="#fff"/></svg>
      <svg width="14" height="14" viewBox="0 0 14 14"><path d="M7 1c3 0 4 2 4 5v3l1.5 2h-11L3 9V6c0-3 1-5 4-5z M5.5 12h3a1.5 1.5 0 0 1-3 0z" fill="#fff"/></svg>
      <svg width="26" height="14" viewBox="0 0 26 14"><circle cx="7" cy="7" r="6" fill="#fff"/><circle cx="7" cy="5.5" r="2.2" fill="#1d1d1d"/><path d="M3.5 11a4 3 0 0 1 7 0" fill="#1d1d1d"/><path d="M18 5l3 3 3-3" fill="none" stroke="#fff" stroke-width="1.6"/></svg>
    </div>
  </div>
  <nav class="abs rail">
    <div class="rail-item" style="top:22px"><svg width="14" height="13" viewBox="0 0 14 13"><path d="M7 0l7 6h-2v7H9V9H5v4H2V6H0z" fill="#fff"/></svg>My QuillVane</div>
    <div class="rail-item" style="top:80px"><svg width="11" height="14" viewBox="0 0 11 14"><path d="M0 0h7l4 4v10H0z" fill="#fff"/><path d="M2 7h7M2 9.5h7" stroke="#0a6ab5"/></svg>My English</div>
    <div class="rail-item" style="top:138px"><svg width="14" height="12" viewBox="0 0 14 12"><rect x="0" y="3" width="14" height="9" rx="1" fill="#fff"/><rect x="4.5" y="0" width="5" height="4" fill="none" stroke="#fff" stroke-width="1.4"/></svg>Business</div>
  </nav>
  <aside class="abs vocab-nav">
    <div class="filter" style="left:12px;top:22px">All <span>⬍</span></div>
    <div class="expand">Expand <svg width="10" height="10" viewBox="0 0 10 10"><path d="M1 4h3V1M9 4H6V1M1 6h3v3M9 6H6v3" fill="none" stroke="#fff"/></svg></div>
    <div class="nav-rule" style="top:73px"></div>
    <div class="group-title" style="top:79px"><svg width="12" height="12" viewBox="0 0 12 12"><circle cx="6" cy="6" r="5" fill="none" stroke="#fff" stroke-width="1.4"/><path d="M6 3v3h2" fill="none" stroke="#fff" stroke-width="1.4"/></svg>Short-Term Memory</div>
    <div class="word active" style="top:110px">Grab</div>
    <div class="nav-rule" style="top:159px"></div>
    <div class="group-title" style="top:170px"><svg width="12" height="12" viewBox="0 0 12 12"><rect x="2" y="2" width="8" height="8" fill="#fff"/><path d="M0 4h12M0 8h12M4 0v12M8 0v12" stroke="#fff"/></svg>Working Memory</div>
    <div class="word" style="top:201px">Cool Down</div>
    <div class="word" style="top:232px">Crave</div>
    <div class="word" style="top:263px">Go For</div>
    <div class="word" style="top:294px">Go-To</div>
    <div class="word" style="top:326px">In The Mood For</div>
    <div class="word" style="top:357px">Sip</div>
    <div class="word" style="top:388px">Soothing</div>
    <div class="word" style="top:419px">Stick With</div>
    <div class="word" style="top:450px">Throw In/Throw On</div>
    <div class="nav-rule" style="top:485px"></div>
    <div class="group-title" style="top:500px"><svg width="11" height="12" viewBox="0 0 11 12"><rect x="0" y="5" width="11" height="7" rx="1" fill="#fff"/><path d="M2.5 5V3.5a3 3 0 0 1 6 0V5" fill="none" stroke="#fff" stroke-width="1.6"/></svg>Long-Term Memory</div>
    <div class="word" style="top:531px">Give It A Try</div>
  </aside>
  <main>
    <div class="abs card"></div>
    <div class="h2" style="top:104px">Progress</div>
    <div class="rule" style="top:146px"></div>
    <div class="step-line"></div>
    <div class="step" style="left:456px"><div class="dot done"><svg width="20" height="16" viewBox="0 0 20 16"><path d="M2 8l6 6L18 2" fill="none" stroke="#fff" stroke-width="3"/></svg></div><div class="step-name">Review 1</div><div class="step-state ok">Completed</div></div>
    <div class="step" style="left:668px"><div class="dot done"><svg width="20" height="16" viewBox="0 0 20 16"><path d="M2 8l6 6L18 2" fill="none" stroke="#fff" stroke-width="3"/></svg></div><div class="step-name">Review 2</div><div class="step-state ok">You are here</div></div>
    <div class="step" style="left:880px"><div class="dot todo">!</div><div class="step-name">Review 3</div><div class="step-state">Unvisited</div></div>
    <div class="step" style="left:1092px"><div class="dot todo">!</div><div class="step-name">Review 4</div><div class="step-state">Unvisited</div></div>
    <div class="rule" style="top:308px"></div>
    <div class="h2" style="top:320px;font-weight:600">Grab <svg width="18" height="17" viewBox="0 0 18 17"><path d="M9 0l2.6 5.6 6.2.7-4.6 4.2 1.3 6.1L9 13.5 3.5 16.6l1.3-6.1L.2 6.3l6.2-.7z" fill="#f5a623"/></svg></div>
    <div class="rule" style="top:357px"></div>
    <div class="abs start-btn"><svg width="12" height="14" viewBox="0 0 12 14"><path d="M0 0l12 7-12 7z" fill="#1e1e1e"/></svg>Start Vocabulary Review Exercise 3</div>
    <p class="body-text" style="top:440px">The word <b>“grab”</b> is most commonly used as a <b>verb</b>, meaning <b>to take something quickly or suddenly.</b> Imagine you’re running late for school. You don’t have time for breakfast, so you quickly <b>“grab”</b> an apple from the kitchen and rush out the door. As you reach the bus stop, your friend waves and says, “Hey! Let’s <b>“grab”</b> a coffee after class.” Later, when you sit down, your phone starts ringing. You <b>“grab”</b> it from your bag and answer.</p>
    <div class="rule" style="top:565px"></div>
    <div class="h2" style="top:575px">Learning Curve Graph</div>
    <div class="rule" style="top:616px"></div>
    <svg class="abs chart" width="790" height="390" viewBox="384 640 790 390" font-family="Poppins, sans-serif">
      <rect x="518" y="670" width="632" height="72" fill="#e5e8ef"/>
      <rect x="518" y="742" width="632" height="71" fill="#e2eae0"/>
      <rect x="518" y="813" width="632" height="70" fill="#eceadd"/>
      <rect x="518" y="883" width="632" height="72" fill="#ecdfe0"/>
      <g stroke="#d8dbe0" stroke-width=".8">
        <path d="M547 665V968M604 665V968M661 665V968M719 665V968M776 665V968M833 665V968M891 665V968M948 665V968M1005 665V968M1063 665V968M1120 665V968"/>
      </g>
      <path d="M518 657V968H1150" fill="none" stroke="#333" stroke-width="1"/>
      <g font-size="11" fill="#222" text-anchor="end">
        <text x="514" y="711">Long-Term Memory</text>
        <text x="514" y="782">Working Memory</text>
        <text x="514" y="852">Short-Term Memory</text>
        <text x="514" y="923">Forgotten Memory</text>
      </g>
      <text x="402" y="812" font-size="11" fill="#222" text-anchor="middle" transform="rotate(-90 402 812)">Memory Zone</text>
      <text x="833" y="1013" font-size="11" fill="#222" text-anchor="middle">Date Range</text>
      <g stroke="#1010d0" stroke-width="1.3">
        <path d="M604 848V919M661 778V919M719 778V919M776 813V919M833 848V919M891 883V919"/>
      </g>
      <path d="M547 919L604 848L661 778L719 778L776 813L833 848L891 883L948 919L1120 919" fill="none" stroke="#1010d0" stroke-width="1.3" stroke-dasharray="4 3"/>
      <g fill="#1010d0">
        <circle cx="547" cy="919" r="2.5"/><circle cx="604" cy="848" r="2.5"/><circle cx="661" cy="778" r="2.5"/><circle cx="719" cy="778" r="2.5"/><circle cx="776" cy="813" r="2.5"/><circle cx="833" cy="848" r="2.5"/><circle cx="891" cy="883" r="2.5"/><circle cx="948" cy="919" r="2.5"/><circle cx="1005" cy="919" r="2.5"/><circle cx="1063" cy="919" r="2.5"/><circle cx="1120" cy="919" r="2.5"/>
      </g>
      <g font-size="8.5" fill="#222" text-anchor="end">
        <text transform="translate(522 976) rotate(-45)" font-size="7">12:00</text>
        <text transform="translate(551 978) rotate(-45)">18 May</text>
        <text transform="translate(579 976) rotate(-45)" font-size="7">12:00</text>
        <text transform="translate(608 978) rotate(-45)">19 May</text>
        <text transform="translate(636 976) rotate(-45)" font-size="7">12:00</text>
        <text transform="translate(665 978) rotate(-45)">20 May</text>
        <text transform="translate(694 976) rotate(-45)" font-size="7">12:00</text>
        <text transform="translate(723 978) rotate(-45)">21 May</text>
        <text transform="translate(751 976) rotate(-45)" font-size="7">12:00</text>
        <text transform="translate(780 978) rotate(-45)">22 May</text>
        <text transform="translate(808 976) rotate(-45)" font-size="7">12:00</text>
        <text transform="translate(837 978) rotate(-45)">23 May</text>
        <text transform="translate(866 976) rotate(-45)" font-size="7">12:00</text>
        <text transform="translate(895 978) rotate(-45)">24 May</text>
        <text transform="translate(923 976) rotate(-45)" font-size="7">12:00</text>
        <text transform="translate(952 978) rotate(-45)">25 May</text>
        <text transform="translate(980 976) rotate(-45)" font-size="7">12:00</text>
        <text transform="translate(1009 978) rotate(-45)">26 May</text>
        <text transform="translate(1038 976) rotate(-45)" font-size="7">12:00</text>
        <text transform="translate(1067 978) rotate(-45)">27 May</text>
        <text transform="translate(1095 976) rotate(-45)" font-size="7">12:00</text>
        <text transform="translate(1124 978) rotate(-45)">28 May</text>
        <text transform="translate(1153 976) rotate(-45)" font-size="7">12:00</text>
      </g>
      <rect x="1023" y="660" width="122" height="73" fill="#fafafa" stroke="#d0d0d0"/>
      <g font-size="8.5" fill="#333">
        <rect x="1028" y="666" width="18" height="6" fill="#e5e8ef"/><text x="1052" y="672">Long-Term Memory</text>
        <rect x="1028" y="679" width="18" height="6" fill="#e2eae0"/><text x="1052" y="685">Working Memory</text>
        <rect x="1028" y="693" width="18" height="6" fill="#eceadd"/><text x="1052" y="699">Short-Term Memory</text>
        <rect x="1028" y="706" width="18" height="6" fill="#ecdfe0"/><text x="1052" y="712">Forgotten Memory</text>
        <rect x="1028" y="720" width="18" height="6" fill="#1010d0"/><text x="1052" y="726">Memory Level</text>
      </g>
    </svg>
    <div class="h2" style="top:1059px;font-size:17px">QuillVane Tutor Learning Analysis</div>
    <p class="body-text" style="top:1100px">Lorem ipsum dolor sit amet, consectetur adipiscing elit. Nam rutrum commodo enim id bibendum. Nunc dignissim risus erat, nec finibus nunc dictum eu. Aliquam sit amet euismod metus, quis malesuada erat. Sed at felis quis nulla feugiat cursus at at dolor. Maecenas pretium aliquet dapibus. Fusce et eleifend massa. Sed convallis ex mi, at vehicula felis commodo molestie. Aliquam dapibus ultrices efficitur. Duis porta mauris eros, at tempus sem tristique eget.</p>
    <div class="abs x10">x10</div>
  </main>
</div>

<!-- Dashboard with expanded vocabulary -->
<div class="screen two">
  <div class="abs app-header">
    <div class="abs brand">QuillVane</div>
    <div class="abs header-icons">
      <svg width="14" height="14" viewBox="0 0 14 14"><circle cx="7" cy="7" r="5" fill="none" stroke="#fff" stroke-width="3" stroke-dasharray="2.4 1.5"/><circle cx="7" cy="7" r="2" fill="#fff"/></svg>
      <svg width="14" height="14" viewBox="0 0 14 14"><path d="M7 1c3 0 4 2 4 5v3l1.5 2h-11L3 9V6c0-3 1-5 4-5z M5.5 12h3a1.5 1.5 0 0 1-3 0z" fill="#fff"/></svg>
      <svg width="26" height="14" viewBox="0 0 26 14"><circle cx="7" cy="7" r="6" fill="#fff"/><circle cx="7" cy="5.5" r="2.2" fill="#1d1d1d"/><path d="M3.5 11a4 3 0 0 1 7 0" fill="#1d1d1d"/><path d="M18 5l3 3 3-3" fill="none" stroke="#fff" stroke-width="1.6"/></svg>
    </div>
  </div>
  <nav class="abs rail">
    <div class="rail-item" style="top:22px"><svg width="14" height="13" viewBox="0 0 14 13"><path d="M7 0l7 6h-2v7H9V9H5v4H2V6H0z" fill="#fff"/></svg>My QuillVane</div>
    <div class="rail-item" style="top:80px"><svg width="11" height="14" viewBox="0 0 11 14"><path d="M0 0h7l4 4v10H0z" fill="#fff"/><path d="M2 7h7M2 9.5h7" stroke="#0a6ab5"/></svg>My English</div>
    <div class="rail-item" style="top:138px"><svg width="14" height="12" viewBox="0 0 14 12"><rect x="0" y="3" width="14" height="9" rx="1" fill="#fff"/><rect x="4.5" y="0" width="5" height="4" fill="none" stroke="#fff" stroke-width="1.4"/></svg>Business</div>
  </nav>
  <aside class="abs vocab-nav">
    <div class="filter" style="left:12px;top:22px">All <span>⬍</span></div>
    <div class="expand">Expand <svg width="10" height="10" viewBox="0 0 10 10"><path d="M1 4h3V1M9 4H6V1M1 6h3v3M9 6H6v3" fill="none" stroke="#fff"/></svg></div>
    <div class="nav-rule" style="top:73px"></div>
    <div class="group-title" style="top:79px">Short-Term Memory</div>
    <div class="word active" style="top:110px">Grab</div>
    <div class="word" style="top:419px">Stick With</div>
    <div class="word" style="top:450px">Throw In/Throw On</div>
    <div class="nav-rule" style="top:485px"></div>
    <div class="group-title" style="top:500px"><svg width="11" height="12" viewBox="0 0 11 12"><rect x="0" y="5" width="11" height="7" rx="1" fill="#fff"/><path d="M2.5 5V3.5a3 3 0 0 1 6 0V5" fill="none" stroke="#fff" stroke-width="1.6"/></svg>Long-Term Memory</div>
    <div class="word" style="top:531px">Give It A Try</div>
  </aside>
  <main>
    <div class="abs card"></div>
    <div class="h2" style="top:104px">Progress</div>
    <div class="rule" style="top:146px"></div>
    <p class="body-text" style="top:440px">The word <b>“grab”</b> is most commonly used as a <b>verb</b>, meaning <b>to take something quickly or suddenly.</b> Imagine you’re running late for school. You don’t have time for breakfast, so you quickly <b>“grab”</b> an apple from the kitchen and rush out the door. As you reach the bus stop, your friend waves and says, “Hey! Let’s <b>“grab”</b> a coffee after class.” Later, when you sit down, your phone starts ringing. You <b>“grab”</b> it from your bag and answer.</p>
    <div class="rule" style="top:565px"></div>
    <div class="h2" style="top:575px">Learning Curve Graph</div>
    <div class="rule" style="top:616px"></div>
    <svg class="abs chart" width="790" height="390" viewBox="384 640 790 390" font-family="Poppins, sans-serif">
      <rect x="518" y="670" width="632" height="72" fill="#e5e8ef"/>
      <rect x="518" y="742" width="632" height="71" fill="#e2eae0"/>
      <rect x="518" y="813" width="632" height="70" fill="#eceadd"/>
      <rect x="518" y="883" width="632" height="72" fill="#ecdfe0"/>
      <path d="M518 657V968H1150" fill="none" stroke="#333"/>
      <g font-size="11" fill="#222" text-anchor="end">
        <text x="514" y="711">Long-Term Memory</text>
        <text x="514" y="782">Working Memory</text>
        <text x="514" y="852">Short-Term Memory</text>
        <text x="514" y="923">Forgotten Memory</text>
      </g>
      <text x="402" y="812" font-size="11" fill="#222" text-anchor="middle" transform="rotate(-90 402 812)">Memory Zone</text>
      <text x="833" y="1013" font-size="11" fill="#222" text-anchor="middle">Date Range</text>
      <path d="M604 848V919M661 778V919M719 778V919M776 813V919M833 848V919M891 883V919" stroke="#1010d0" stroke-width="1.3"/>
      <path d="M547 919L604 848L661 778L719 778L776 813L833 848L891 883L948 919L1120 919" fill="none" stroke="#1010d0" stroke-width="1.3" stroke-dasharray="4 3"/>
      <g font-size="8.5" fill="#222" text-anchor="end">
        <text transform="translate(551 978) rotate(-45)">18 May</text><text transform="translate(608 978) rotate(-45)">19 May</text><text transform="translate(665 978) rotate(-45)">20 May</text><text transform="translate(723 978) rotate(-45)">21 May</text><text transform="translate(780 978) rotate(-45)">22 May</text><text transform="translate(837 978) rotate(-45)">23 May</text><text transform="translate(895 978) rotate(-45)">24 May</text><text transform="translate(952 978) rotate(-45)">25 May</text><text transform="translate(1009 978) rotate(-45)">26 May</text><text transform="translate(1067 978) rotate(-45)">27 May</text><text transform="translate(1124 978) rotate(-45)">28 May</text>
      </g>
      <rect x="1023" y="660" width="122" height="73" fill="#fafafa" stroke="#d0d0d0"/>
      <g font-size="8.5" fill="#333">
        <text x="1052" y="672">Long-Term Memory</text><text x="1052" y="685">Working Memory</text><text x="1052" y="699">Short-Term Memory</text><text x="1052" y="712">Forgotten Memory</text>
        <rect x="1028" y="720" width="18" height="6" fill="#1010d0"/><text x="1052" y="726">Memory Level</text>
      </g>
    </svg>
    <div class="h2" style="top:1059px;font-size:17px">QuillVane Tutor Learning Analysis</div>
    <p class="body-text" style="top:1100px">Lorem ipsum dolor sit amet, consectetur adipiscing elit. Nam rutrum commodo enim id bibendum. Nunc dignissim risus erat, nec finibus nunc dictum eu. Aliquam sit amet euismod metus, quis malesuada erat. Sed at felis quis nulla feugiat cursus at at dolor. Maecenas pretium aliquet dapibus. Fusce et eleifend massa. Sed convallis ex mi, at vehicula felis commodo molestie. Aliquam dapibus ultrices efficitur. Duis porta mauris eros, at tempus sem tristique eget.</p>
    <div class="abs x10">x10</div>
  </main>
  <div class="abs overlay"></div>
  <section class="abs modal">
    <div class="filter light" style="left:25px;top:22px">All <span>⬍</span></div>
    <svg class="abs" style="left:982px;top:30px" width="16" height="14" viewBox="0 0 16 14"><rect x="1" y="1" width="14" height="12" fill="none" stroke="#777" stroke-width="1.5"/><path d="M5 4l6 6M11 4l-6 6" stroke="#777" stroke-width="1.5"/></svg>
    <div class="m-title" style="top:76px"><svg width="12" height="12" viewBox="0 0 12 12"><circle cx="6" cy="6" r="5" fill="none" stroke="#1e1e1e" stroke-width="1.4"/><path d="M6 3v3h2" fill="none" stroke="#1e1e1e" stroke-width="1.4"/></svg>Short-Term Memory</div>
    <div class="m-row" style="top:114px"><span class="sel">Grab</span></div>
    <div class="m-rule" style="top:148px"></div>
    <div class="m-title" style="top:164px"><svg width="12" height="12" viewBox="0 0 12 12"><rect x="2" y="2" width="8" height="8" fill="#1e1e1e"/><path d="M0 4h12M0 8h12M4 0v12M8 0v12" stroke="#1e1e1e"/></svg>Working Memory</div>
    <div class="m-row" style="top:195px"><span>Cool Down</span><span>Crave</span><span>Go For</span><span>Go-To</span><span>In The Mood For</span><span>Sip</span><span>Soothing</span><span>Stick With</span><span>Throw In/Throw On</span></div>
    <div class="m-rule" style="top:232px"></div>
    <div class="m-title" style="top:245px"><svg width="11" height="12" viewBox="0 0 11 12"><rect x="0" y="5" width="11" height="7" rx="1" fill="#1e1e1e"/><path d="M2.5 5V3.5a3 3 0 0 1 6 0V5" fill="none" stroke="#1e1e1e" stroke-width="1.6"/></svg>Long-Term Memory</div>
    <div class="m-row" style="top:276px"><span>Give It A Try</span></div>
  </section>
</div>

</body>
</html>
```